AI Business Tools Landing Page

My web-based website builder (Pavlora.com) will be adding many new features in the very near future and I need an eye-catching landing page to promote these new products.

The page will have a primary section of the 8 main products we are promoting:
1. AI Instant Website Generator
2. AI Chatbot
3. Online Store Builder with AI Assistance
4. AI Auto-Blogging System
5. Online Scheduling System
6. Custom Email System
7. SEO Service
8. CRM System

The page will also have a smaller section for links to our affiliate programs. These can be smaller, less-promanent buttons or links. These are the affiliate products:
1. Get Your LLC
2. Website Design and Maintenance
3. Searchly Ads Management
4. Social Media Posting Service
5. Logo Design
6. Trademark Registration
7. Patent Application
8. Printing Services (including postcards, flyers, and merch.)
9. Bulk AI Content Generator

The theme and color scheme of the page should follow the theme of our main website, which is https://pavlora.com.

I need the page fully coded and ready to deploy on my server.

I look forward to seeing your amazing designs!

```html
<!DOCTYPE html>
<html lang="en">
<head>
<meta charset="UTF-8">
<title>Pavlora – AI Business Tools</title>
<link rel="stylesheet" href="https://fonts.googleapis.com/css2?family=Poppins:wght@400;500;600;700&display=swap">
<style>
  :root {
    --navy: #061a4a;
    --deep: #0a2a78;
    --blue: #0b7df0;
    --sky: #1ea0ff;
    --ink: #1b1b1f;
    --muted: #666a73;
    --card: #efeff1;
    --white: #ffffff;
  }
  * { box-sizing: border-box; margin: 0; padding: 0; }
  html, body { width: 1200px; height: 2588px; overflow: hidden; }
  body { font-family: "Poppins", sans-serif; color: var(--ink); background: var(--white); position: relative; }

  /* Hero */
  .hero { position: absolute; top: 0; left: 0; width: 1200px; height: 480px;
    background: linear-gradient(100deg, var(--navy) 0%, var(--deep) 55%, #0d3fa8 100%); overflow: hidden; }
  .hero-visual { position: absolute; right: 0; top: 0; width: 640px; height: 420px;
    background: radial-gradient(ellipse at 55% 45%, #3fa9ff 0%, #1464d8 35%, rgba(10,42,120,0) 72%); }
  .hero-wave { position: absolute; left: 0; bottom: 0; width: 1200px; height: 130px; }
  .brand { position: absolute; top: 26px; left: 40px; display: flex; align-items: center; gap: 12px;
    color: var(--white); font-weight: 700; font-size: 30px; }
  .brand-dot { width: 34px; height: 34px; border-radius: 50%; background: var(--sky); }
  .menu { position: absolute; top: 34px; right: 60px; display: flex; align-items: center; gap: 12px;
    color: var(--white); font-size: 16px; font-weight: 500; }
  .menu-bars { width: 24px; height: 16px; display: flex; flex-direction: column; justify-content: space-between; }
  .menu-bars span { height: 3px; background: var(--white); border-radius: 2px; }
  .hero-copy { position: absolute; left: 120px; top: 168px; color: var(--white); }
  .hero-kicker { font-size: 22px; font-weight: 500; }
  .hero-title { font-size: 50px; font-weight: 700; line-height: 1.15; margin-top: 2px; }
  .btn { display: inline-block; background: var(--sky); color: var(--white); font-weight: 500;
    font-size: 17px; border-radius: 6px; padding: 12px 32px; text-decoration: none; }
  .hero .btn { margin-top: 26px; }

  /* Tools */
  .tools { position: absolute; top: 540px; left: 0; width: 1200px; }
  .section-title { margin-left: 120px; font-size: 40px; font-weight: 700; }
  .tool-grid { position: absolute; top: 100px; left: 210px; width: 780px;
    display: flex; flex-wrap: wrap; justify-content: center; column-gap: 30px; row-gap: 30px; }
  .tool-card { width: 240px; background: var(--card); height: 280px; padding: 20px 18px; text-align: center; }
  .tool-icon { width: 84px; height: 84px; margin: 0 auto 12px; border-radius: 50%;
    border: 4px solid var(--sky); background: var(--white); display: flex; align-items: center; justify-content: center; }
  .tool-icon svg { width: 42px; height: 42px; }
  .tool-name { font-size: 19px; font-weight: 600; line-height: 1.25; margin-bottom: 10px; }
  .tool-text { font-size: 12.5px; color: var(--muted); line-height: 1.5; }
  .view-all { position: absolute; top: 1030px; left: 508px; width: 184px; text-align: center; }

  /* Resources */
  .resources { position: absolute; top: 1660px; left: 0; width: 1200px; height: 760px;
    background: linear-gradient(180deg, #128ef5 0%, var(--blue) 100%); }
  .resources-top { position: absolute; top: 0; left: 0; width: 1200px; height: 90px; }
  .resources-title { position: absolute; top: 100px; width: 1200px; text-align: center;
    color: var(--white); font-size: 48px; font-weight: 700; line-height: 1.3; }
  .resources-visual { position: absolute; top: 250px; left: 152px; width: 410px; height: 450px; border-radius: 8px;
    background: linear-gradient(160deg, #c7d3df 0%, #7e95b3 45%, #2c4a8a 100%); }
  .affiliate-list { position: absolute; top: 268px; left: 608px; list-style: none; }
  .affiliate-list li { display: flex; align-items: center; gap: 16px; color: var(--white);
    font-size: 19px; font-weight: 500; height: 44px; }
  .affiliate-list li.wrap { height: 66px; align-items: flex-start; line-height: 1.55; padding-top: 6px; }
  .affiliate-list svg { width: 18px; height: 18px; flex: none; }
  .affiliate-list li.wrap svg { margin-top: 6px; }

  /* Footer */
  .footer-curve { position: absolute; top: 2330px; left: 0; width: 1200px; height: 91px; }
  .footer-brand { position: absolute; top: 2400px; left: 780px; display: flex; align-items: center; gap: 14px;
    font-size: 46px; font-weight: 700; color: var(--ink); }
  .footer-brand .brand-dot { width: 52px; height: 52px; background: var(--blue); }
  .footer-links { position: absolute; top: 2495px; left: 110px; width: 560px;
    display: flex; flex-wrap: wrap; column-gap: 24px; row-gap: 8px; }
  .footer-links a { font-size: 15px; color: var(--ink); text-decoration: none; font-weight: 500; }
  .copyright { position: absolute; top: 2497px; left: 780px; font-size: 15px; font-weight: 500; }
  .social { position: absolute; top: 2535px; left: 780px; display: flex; gap: 12px; }
  .social span { width: 18px; height: 18px; border-radius: 50%; background: var(--ink); }
</style>
</head>
<body>

<header class="hero">
  <div class="hero-visual" role="img" aria-label="Photo of a hand reaching toward glowing AI assistant icons"></div>
  <div class="brand"><span class="brand-dot"></span>Pavlora</div>
  <div class="menu">Menu <span class="menu-bars"><span></span><span></span><span></span></span></div>
  <div class="hero-copy">
    <p class="hero-kicker">Welcome To</p>
    <h1 class="hero-title">AI Business Tools</h1>
    <a class="btn" href="https://pavlora.com">Get Started</a>
  </div>
  <svg class="hero-wave" viewBox="0 0 1200 130" preserveAspectRatio="none" aria-hidden="true">
    <path d="M0 40 C 300 140, 800 130, 1200 20 L1200 130 L0 130 Z" fill="#ffffff"/>
  </svg>
</header>

<section class="tools">
  <h2 class="section-title">AI Business Tools</h2>
  <div class="tool-grid">
    <article class="tool-card">
      <div class="tool-icon"><svg viewBox="0 0 48 48" fill="none" stroke="#1b1b1f" stroke-width="2.5"><circle cx="24" cy="24" r="18"/><ellipse cx="24" cy="24" rx="8" ry="18"/><path d="M6 24h36M9 14h30M9 34h30"/></svg></div>
      <h3 class="tool-name">AI Instant Website Generator</h3>
      <p class="tool-text">Describe your business and our AI builds a complete, responsive website with pages and copy in seconds.</p>
    </article>
    <article class="tool-card">
      <div class="tool-icon"><svg viewBox="0 0 48 48" fill="none" stroke="#1b1b1f" stroke-width="2.5"><path d="M8 10h32v22H20l-8 7v-7H8z"/><circle cx="17" cy="21" r="1.5" fill="#1b1b1f"/><circle cx="24" cy="21" r="1.5" fill="#1b1b1f"/><circle cx="31" cy="21" r="1.5" fill="#1b1b1f"/></svg></div>
      <h3 class="tool-name">AI ChatBot</h3>
      <p class="tool-text">A chatbot trained on your content answers visitor questions, books calls and captures leads day and night.</p>
    </article>
    <article class="tool-card">
      <div class="tool-icon"><svg viewBox="0 0 48 48" fill="none" stroke="#1b1b1f" stroke-width="2.5"><path d="M5 8h6l5 22h22l4-15H13"/><circle cx="19" cy="37" r="3"/><circle cx="35" cy="37" r="3"/></svg></div>
      <h3 class="tool-name">Online Store Builder (E-Commerce) with AI Assistance</h3>
      <p class="tool-text">Launch a shop with AI-written listings, then manage stock, orders and payments from one dashboard.</p>
    </article>
    <article class="tool-card">
      <div class="tool-icon"><svg viewBox="0 0 48 48" fill="none" stroke="#1b1b1f" stroke-width="2.5"><path d="M10 38l4-12 20-20 8 8-20 20z"/><path d="M30 10l8 8M10 38l12-4"/></svg></div>
      <h3 class="tool-name">AI Auto-Blogging System</h3>
      <p class="tool-text">Pick topics and a schedule, and fresh articles are written and posted to your blog automatically.</p>
    </article>
    <article class="tool-card">
      <div class="tool-icon"><svg viewBox="0 0 48 48" fill="none" stroke="#1b1b1f" stroke-width="2.5"><rect x="7" y="10" width="34" height="30" rx="3"/><path d="M7 18h34M15 6v8M33 6v8M14 26h5M22 26h5M30 26h5M14 33h5M22 33h5"/></svg></div>
      <h3 class="tool-name">Online Scheduling System</h3>
      <p class="tool-text">Let clients book appointments online, sync your calendars and send reminders to cut missed meetings.</p>
    </article>
    <article class="tool-card">
      <div class="tool-icon"><svg viewBox="0 0 48 48" fill="none" stroke="#1b1b1f" stroke-width="2.5"><rect x="6" y="12" width="36" height="24" rx="2"/><path d="M6 14l18 13 18-13"/></svg></div>
      <h3 class="tool-name">Custom emails using your domain</h3>
      <p class="tool-text">Create professional addresses on your own domain with team inboxes, aliases and easy forwarding.</p>
    </article>
    <article class="tool-card">
      <div class="tool-icon"><svg viewBox="0 0 48 48" fill="none" stroke="#1b1b1f" stroke-width="2.5"><circle cx="21" cy="21" r="12"/><path d="M30 30l11 11"/></svg></div>
      <h3 class="tool-name">SEO Service</h3>
      <p class="tool-text">Climb search results with keyword research, on-page fixes and monthly reports from our SEO team.</p>
    </article>
    <article class="tool-card">
      <div class="tool-icon"><svg viewBox="0 0 48 48" fill="none" stroke="#1b1b1f" stroke-width="2.5"><rect x="7" y="9" width="34" height="30" rx="3"/><path d="M13 17h22M13 24h22M13 31h14"/></svg></div>
      <h3 class="tool-name">CRM System</h3>
      <p class="tool-text">Keep every contact, deal and conversation in one place and follow up with customers on time.</p>
    </article>
  </div>
  <a class="btn view-all" href="https://pavlora.com">View All</a>
</section>

<section class="resources">
  <svg class="resources-top" viewBox="0 0 1200 90" preserveAspectRatio="none" aria-hidden="true">
    <path d="M0 0 L1200 0 L1200 10 C 800 90, 400 90, 0 30 Z" fill="#ffffff"/>
  </svg>
  <h2 class="resources-title">Additional Resources to Help<br>Launch Your Business</h2>
  <div class="resources-visual" role="img" aria-label="Photo of a smiling woman using her smartphone"></div>
  <ul class="affiliate-list">
    <li><svg viewBox="0 0 18 18"><path d="M5 3l7 6-7 6" fill="none" stroke="#fff" stroke-width="3"/></svg>Get Your LLC</li>
    <li><svg viewBox="0 0 18 18"><path d="M5 3l7 6-7 6" fill="none" stroke="#fff" stroke-width="3"/></svg>Website Design and Maintenance</li>
    <li><svg viewBox="0 0 18 18"><path d="M5 3l7 6-7 6" fill="none" stroke="#fff" stroke-width="3"/></svg>Searchly Ads Management</li>
    <li><svg viewBox="0 0 18 18"><path d="M5 3l7 6-7 6" fill="none" stroke="#fff" stroke-width="3"/></svg>Social Media Posting Service</li>
    <li><svg viewBox="0 0 18 18"><path d="M5 3l7 6-7 6" fill="none" stroke="#fff" stroke-width="3"/></svg>Logo Design</li>
    <li><svg viewBox="0 0 18 18"><path d="M5 3l7 6-7 6" fill="none" stroke="#fff" stroke-width="3"/></svg>Trademark Registration</li>
    <li><svg viewBox="0 0 18 18"><path d="M5 3l7 6-7 6" fill="none" stroke="#fff" stroke-width="3"/></svg>Patent Application</li>
    <li class="wrap"><svg viewBox="0 0 18 18"><path d="M5 3l7 6-7 6" fill="none" stroke="#fff" stroke-width="3"/></svg><span>Printing Services (including postcards, flyers,<br>and merch.)</span></li>
    <li><svg viewBox="0 0 18 18"><path d="M5 3l7 6-7 6" fill="none" stroke="#fff" stroke-width="3"/></svg>Bulk AI Content Generator</li>
  </ul>
</section>

<svg class="footer-curve" viewBox="0 0 1200 91" preserveAspectRatio="none" aria-hidden="true">
  <path d="M0 85 C 400 95, 800 75, 1200 0 L1200 91 L0 91 Z" fill="#ffffff"/>
</svg>

<footer>
  <div class="footer-brand"><span class="brand-dot"></span>Pavlora</div>
  <nav class="footer-links">
    <a href="https://pavlora.com">About Pavlora</a>
    <a href="https://pavlora.com">Learn More About AI</a>
    <a href="https://pavlora.com">Make Money with Pavlora</a>
    <a href="https://pavlora.com">The History of AI</a>
    <a href="https://pavlora.com">Pricing</a>
    <a href="https://pavlora.com">Blog</a>
    <a href="https://pavlora.com">Sitemap</a>
  </nav>
  <p class="copyright">© 2024 Pavlora. All Rights Reserved</p>
  <div class="social" aria-label="Social links">
    <span></span><span></span><span></span><span></span><span></span><span></span><span></span><span></span><span></span><span></span>
  </div>
</footer>

</body>
</html>
```